@CLLovedale Meaddow Company

Honey Jar label. Would like it to be square (diamond shape). Will need a space for my city and state. will need a space for my phone number. Will need to have "Grade A" on the label and "product of USA" "Honey" must be larger then any other word. Black background. Label needs to look old fashion (cir 1880s) Sketch of Mt #2Raainier attached that I have the rights to use.

Like the look of this https://shop.pellowbrint.com/pbshop/item.php?nodeid=16

Same label will also be used for a run of a limited supply of honey. So I will need one that also has "Pipkin's private batch". Pipkin is my daughter"s rabbit

```html
<!DOCTYPE html>
<html lang="en">
<head>
<meta charset="utf-8">
<title>CLLovedale Meaddow Company – Honey Labels</title>
<link rel="stylesheet" href="https://fonts.googleapis.com/css2?family=Smythe&family=Playfair+Display:ital@1&family=Cinzel:wght@600&display=swap">
<style>
  :root {
    --bg-top: #f0d9a0;
    --bg-mid: #dea538;
    --bg-bottom: #d15300;
    --ink: #5a2208;
    --ornament: #9a5a12;
    --cream: #fff6df;
    --hairline: rgba(255, 240, 200, 0.45);
    --ribbon: #9a5a10;
    --ribbon-edge: #f3d28a;
  }
  html, body {
    margin: 0;
    width: 1200px;
    height: 900px;
    overflow: hidden;
  }
  body {
    background: linear-gradient(to bottom, var(--bg-top) 0%, var(--bg-mid) 35%, var(--bg-bottom) 100%);
  }
  .label-sheet {
    display: block;
    width: 1200px;
    height: 900px;
  }
  .diamond-frame { fill: none; stroke: var(--hairline); stroke-width: 1; }
  .inner-line { stroke: var(--cream); stroke-width: 1.2; opacity: 0.85; }
  .rule { stroke: var(--ornament); stroke-width: 1.2; }
  .ornament-area { fill: var(--ornament); opacity: 0.75; }
  .scene-ring { fill: none; stroke: var(--ribbon-edge); stroke-width: 2; }
  .company-name { font-family: "Smythe", serif; font-size: 25px; fill: var(--ink); }
  .script { font-family: "Playfair Display", serif; font-style: italic; font-size: 21px; fill: var(--cream); }
  .stamp { font-family: "Smythe", serif; font-size: 44px; fill: var(--ink); }
  .edge-text { font-family: "Cinzel", serif; font-weight: 600; font-size: 12px; fill: var(--cream); letter-spacing: 0.5px; }
  .product-name { font-family: "Smythe", serif; font-size: 128px; fill: var(--ink); }
  .ribbon { fill: var(--ribbon); stroke: var(--ribbon-edge); stroke-width: 1; }
  .ribbon-text { font-family: "Cinzel", serif; font-weight: 600; font-size: 13px; fill: var(--cream); letter-spacing: 1px; }
</style>
</head>
<body>
<svg class="label-sheet" viewBox="0 0 1200 900" xmlns="http://www.w3.org/2000/svg">
  <defs>
    <linearGradient id="scene-tones" x1="0" y1="0" x2="0" y2="1">
      <stop offset="0" stop-color="#e9efe0"/>
      <stop offset="0.45" stop-color="#b96a5c"/>
      <stop offset="0.65" stop-color="#e08a4a"/>
      <stop offset="1" stop-color="#7a9a2e"/>
    </linearGradient>
    <path id="name-arc" d="M180,334 Q307,290 434,334"/>
    <path id="ribbon-arc" d="M770,501 Q893,474 1016,501"/>

    <g id="label-base">
      <polygon class="diamond-frame" points="307,158 599,450 307,742 15,450"/>
      <line class="inner-line" x1="80" y1="400" x2="213" y2="268"/>
      <line class="inner-line" x1="402" y1="268" x2="535" y2="400"/>

      <rect class="ornament-area" x="222" y="190" width="170" height="72" rx="36" role="img" aria-label="Victorian scroll ornament"/>
      <line class="rule" x1="222" y1="270" x2="392" y2="270"/>
      <line class="rule" x1="222" y1="276" x2="392" y2="276"/>

      <text class="company-name" text-anchor="middle" textLength="205" lengthAdjust="spacingAndGlyphs"><textPath href="#name-arc" startOffset="50%">CLLOVEDALE MEADDOW CO.</textPath></text>

      <ellipse class="scene-ring" cx="307" cy="418" rx="131" ry="91"/>
      <ellipse cx="307" cy="418" rx="124" ry="84" fill="url(#scene-tones)" role="img" aria-label="Sketch of a snow-capped mountain under clouds above green forest"/>

      <text class="script" x="108" y="432" text-anchor="middle">Product of</text>
      <text class="stamp" x="108" y="476" text-anchor="middle">USA</text>
      <text class="script" x="498" y="438" text-anchor="middle">Grade</text>
      <text class="stamp" x="498" y="482" text-anchor="middle">A</text>

      <text class="edge-text" transform="translate(82,494) rotate(45)" textLength="150" lengthAdjust="spacingAndGlyphs">TEL. 1-800-555-0142</text>
      <text class="edge-text" transform="translate(430,600) rotate(-45)" textLength="172" lengthAdjust="spacingAndGlyphs">ALDER SPRINGS, OREGON</text>

      <text class="product-name" x="307" y="606" text-anchor="middle" textLength="205" lengthAdjust="spacingAndGlyphs">HONEY</text>

      <line class="rule" x1="222" y1="620" x2="392" y2="620"/>
      <line class="rule" x1="222" y1="626" x2="392" y2="626"/>
      <rect class="ornament-area" x="222" y="634" width="170" height="74" rx="37" role="img" aria-label="Victorian scroll ornament"/>
    </g>
  </defs>

  <g class="label label-standard">
    <use href="#label-base"/>
  </g>

  <g class="label label-private-batch">
    <use href="#label-base" transform="translate(586,0)"/>
    <path class="ribbon" d="M764,484 Q893,456 1020,484 L1016,514 Q893,488 768,516 Z"/>
    <text class="ribbon-text" text-anchor="middle" textLength="220" lengthAdjust="spacingAndGlyphs"><textPath href="#ribbon-arc" startOffset="50%">PIPKIN'S PRIVATE BATCH</textPath></text>
  </g>
</svg>
</body>
</html>
```